Wordpress Design Project - Leadership Guide Nest

Website Brief

We are looking to have a design produced for a modern professional website. A mind map of the site can be found here: http://www.thoughtlattice.example/view.htm?m=58142736a1b94c07d2e5f8a3c6b71d09

Each of the green tabs are pages just next to them is a very small green globe. If you click this. It will take you through to an example page for that section.

Task description
The website will be made up of:
1. A homepage (this will be the blog see http://www.janetquillby.example for an example of the crisp and cleanness we are looking for)
2. A page that will have just a video and option page (see: http://tvpgacademy.example/ for example)
3. 3 pages all with the same structure. (see: http://tvpgacademy.example/qw72plx19bnv/ for an example). Each will have:
a. A video
b. Tabs at the top of the video that link to the 3 videos and the sales page
c. Link to a resource download
d. Circlebook Comments section
4. 2 Page with about the experts and about our company (same style for both)
5. A page that will have a long well designed sales page (see: http://tvpgacademy.example/early-enrollment-2013/ for an example)
6. A page with testimonials on it (see http://www.janetquillby.example/praise/)
7. A page that will describe the products, services and provision we will be offering
8. A page that will detail our involvement with charities and not for profits

Must Have
Edgey, crisp design, similar to Janet Quillbys. We would like the colours to match very well throughout the site and have a unique font (possibly manksans). We want it to have very clean integrations between copy and images with shadows on videos for example like with Janetquillbys page. We really love this design and would like this to be the inspiration for our site however it would need to certainly have a more executive feel to suit our target market.

We like the idea of some kind of circles, crisp clean lines, nice white space, simple design, corporate looking, communicates wealth/success/massive value. Based on the two logos of NDLTR and the Hub (see attached)

Target Market:
The target market includes intelligent, productive coaches, who are self employed or part of small firms. They are well educated, well read, socially conscious, and committed to making a profound difference with their clients...skilled at the actions of coaching, but not the business side. There will be a ratio of approximately 60% male / 40% female (really? The coaching industry is predominantly female, no?), with an age range of 40 to 60 years. English is our core language. Most will have secondary education and the salary range will be $90,000 to $400,000. We will have a global audience reach, although the primary markets will be North America, Europe and Australia/NZ.

Marketing Objective:
LGN will be an on-line resource for Executive Coaches. The intent of the design will be to present LGN to the world as a highly professional organization. The intent is not to characterize LGN as solely corporate, but will also incorporate elements of entrepreneurialism. We require the brand to incorporate these values:
• Trustworthy – you can trust us
• Professional – we are true professionals whose mission is to provide value to our clients
• Caring - Interested in our clients wellbeing – we are keenly interested in helping our clients build their knowledge, skills, and attitudes to be highly productive and successful
• Successful
• Knowledgeable – we have breadth and depth of knowledge in leadership
• World-class – we have a world-wide target market and, as such, need the brand to reflect a powerful and inclusive image
• Positive Energy - I would like the brand to have positive energy and very clean feng shui
• Prestige
• Massive Value
• Accessible
• Worldly/ Sophisticated
• Affordable
• Mission-critical

Details about the needs, wants, aspirations etc. of our target market
Executive coaches need a process and a system for creating opportunities to do the work they love with clients who are qualified to engage them and pay them. There is a scarcity mentality around their own finances, but ironically an abundance mentality for what's possible in the world and for their clients. They want to make a difference, they want to facilitate transformation, they want to be of deep service.

They aspire to make a decent living doing it! They need help bridging the gap between practitioner/service provider and financially successful entrepreneur/business owner/ leader. They also aspire to have it be easy, as it feels hard for them to generate the revenues they want to generate solely through coaching, so many turn to training, speaking, and other revenue streams.

Required assets to send through to web designer
1. Three blog posts. Each will have:
a. A video/audio
b. Summary of the points raised
c. Download (possibly slides)
2. A page that will have just a video and option page
a. Headline
b. Video
c. One paragraph summary of what we do
3. 3 launch videos. Here for each we will need
a. A video scripted and produced
b. Title for each
c. A resource download
4. Sales page
a. Video
b. Copy
i. Overview
ii. Content of course
iii. Guarentee
iv. Details of bonuses
v. Details of support
vi. Pricing broken down ($30,000 value = $2000)
c. Animated Gif
5. About the company and experts
a. Description of our company, it's vision, mission, purpose and core values.
b. Description of each of us,
i. our key facts and wows,
ii. a picture of us
iii. some interesting facts (giving personality)
iv. Lower down we will add in "Faculty" these will be any thought leaders we invite in to be part of the value delivery (will add to our credibility having such a strong team behind the project)
6. Testimonials
a. Testimonials from coaches from working with us
7. Products, services and provision we will be offering
a. A simple description of each of the key products/services we will be offering
i. Leadership Guide Sales
ii. Leadership Guide Marketing
iii. Leadership Guide Help
iv. Leadership Guide Roundtable
v. Leadership Guide Resources
a. List of the various charity work each of us have been involved with

Requirements
Must have
• Edgey, crisp design, similar to Janet Quillbys. We would like the colours to match very well throughout the site and have a unique font (possibly manksans). We want it to have very clean integrations between copy and images with shadows on videos for example like with Janetquillbys page. We really love this design and would like this to be the inspiration for our site however it would need to certainly have a more executive feel to suit our target market.

```html
<!DOCTYPE html>
<html lang="en">
<head>
<meta charset="utf-8">
<title>Leadership Guide Nest</title>
<link rel="stylesheet" href="https://fonts.googleapis.com/css2?family=Ubuntu:wght@300;400;500&display=swap">
<style>
:root{
  --gold:#e7b04f;
  --gold-deep:#d99a3a;
  --charcoal:#2a2a2a;
  --page:#ececec;
  --panel:#f7f7f7;
  --white:#ffffff;
  --ink:#3a3a3a;
  --muted:#7a7a7a;
  --line:#dcdcdc;
  --green:#8dc55f;
  --green-deep:#74ad49;
  --accent:#f2a623;
  --social:#97a9cf;
  --social-deep:#5b77ab;
  --link:#3d5a9a;
}
*{box-sizing:border-box;margin:0;padding:0}
html,body{width:1200px;height:2317px;overflow:hidden}
body{position:relative;background:var(--page);font-family:"Ubuntu",sans-serif;color:var(--ink)}
.abs{position:absolute}

/* header */
.site-header{position:absolute;left:0;top:0;width:1200px;height:219px;background:var(--white)}
.utility-links{position:absolute;right:98px;top:33px;font-size:13px;color:#222}
.brand{position:absolute;left:98px;top:182px;display:flex;align-items:center;gap:10px}
.brand-dot{width:22px;height:22px;border-radius:50%;background:var(--gold)}
.brand-name{font-size:15px;font-weight:400;color:#8a8a8a}
.search{position:absolute;left:927px;top:116px;width:176px;height:24px;border:1px solid #bdbdbd;border-radius:12px;background:#f4f4f4;box-shadow:inset 0 1px 2px rgba(0,0,0,.15);display:flex;align-items:center;padding-left:10px;gap:8px;font-size:14px;color:#999}
.main-nav{position:absolute;left:374px;top:153px;width:729px;height:48px;background:var(--gold)}
.nav-home{position:absolute;left:0;top:0;width:117px;height:48px;background:var(--gold-deep);display:flex;align-items:center;justify-content:center}
.nav-item{position:absolute;top:14px;font-size:16px;color:var(--white);font-weight:400}

/* hero */
.hero-band{position:absolute;left:0;top:219px;width:1200px;height:402px;background:var(--charcoal)}
.hero-strip{position:absolute;left:0;top:621px;width:1200px;height:12px;background:var(--white)}
.hero-shadow{position:absolute;left:160px;top:722px;width:880px;height:34px;border-radius:50%;background:rgba(0,0,0,.28);filter:blur(10px)}
.hero{position:absolute;left:99px;top:255px;width:1004px;height:479px;background:linear-gradient(100deg,#d9d6d2 0%,#b49378 30%,#e2d4c7 55%,#a68468 78%,#c9b2a0 100%);overflow:hidden}
.slider-dots{position:absolute;left:35px;top:32px;display:flex;gap:11px}
.slider-dots span{width:14px;height:14px;border-radius:50%;background:#bdbdbd;box-shadow:inset 0 1px 2px rgba(0,0,0,.3)}
.slider-dots .active{background:#e8822e}
.hero-caption{position:absolute;left:0;top:264px;width:488px;height:187px;background:rgba(40,40,40,.82);padding:22px 20px}
.hero-title{font-size:35px;font-weight:300;color:var(--accent);line-height:1}
.hero-text{margin-top:10px;font-size:14.5px;line-height:20px;color:#eee;font-weight:300;width:410px}
.resource-btn{position:absolute;left:20px;top:134px;width:279px;height:36px;border-radius:18px;background:linear-gradient(#f6cf7c,#e5a940);border:1px solid #c68a2a;display:flex;align-items:center;padding-left:18px;gap:10px;font-size:18px;color:#3a2a10}
.resource-btn .plus{width:22px;height:22px;border-radius:50%;background:#fff;display:flex;align-items:center;justify-content:center}

/* section headings */
.section-title{position:absolute;font-size:20px;font-weight:400;color:#222;letter-spacing:.3px}

/* videos */
.panel{position:absolute;background:var(--panel);border:1px solid #e2e2e2}
.video-main{position:absolute;left:22px;top:18px;width:446px;height:248px;background:#111}
.video-picture{position:absolute;left:0;top:0;width:446px;height:218px;background:linear-gradient(95deg,#b84a3c 0%,#c9a58d 35%,#e8d9c8 60%,#c79a7c 85%,#8a7a70 100%)}
.play-overlay{position:absolute;left:195px;top:90px}
.video-controls{position:absolute;left:0;top:218px;width:446px;height:30px;background:#151515;display:flex;align-items:center;padding:0 10px;gap:10px;font-size:9px;color:#ccc}
.progress{flex:1;height:4px;background:#555;border-radius:2px;position:relative}
.progress i{position:absolute;left:0;top:0;height:4px;width:46%;background:var(--accent);border-radius:2px}
.progress b{position:absolute;left:46%;top:-4px;width:11px;height:11px;border-radius:50%;background:#fff;margin-left:-5px}
.thumb{position:absolute;left:494px;width:112px;height:62px;background:linear-gradient(110deg,#7f8b96,#d4c6b7 50%,#4e5660)}

/* form */
.field{position:absolute;left:15px;width:320px;background:var(--white);border:1px solid #e4e4e4;font-size:12px;color:#555;padding:9px 12px}
.submit-btn{position:absolute;left:102px;top:246px;width:148px;height:28px;background:var(--green);color:#fff;font-size:15px;display:flex;align-items:center;justify-content:center;letter-spacing:.5px}

/* blog */
.post{position:absolute;left:96px;width:631px;height:284px;background:var(--panel);border:1px solid #e2e2e2}
.post-head{height:54px;background:var(--gold);color:#fff;font-size:15px;padding:18px 22px;text-transform:uppercase;letter-spacing:.2px}
.post-image{position:absolute;left:17px;top:65px;width:202px;height:134px;border:5px solid #fff;box-shadow:0 1px 5px rgba(0,0,0,.35)}
.post-text{position:absolute;left:236px;top:63px;width:374px;font-size:11.2px;line-height:17px;color:#555;font-weight:300;text-align:justify;letter-spacing:-.1px}
.read-more{position:absolute;left:480px;top:196px;width:127px;height:19px;border-radius:10px;background:linear-gradient(#a9d67f,var(--green-deep));color:#fff;font-size:11px;display:flex;align-items:center;justify-content:center}
.share-row{position:absolute;left:9px;top:230px;width:613px;height:40px;background:var(--white);border:1px solid #e2e2e2;display:flex;align-items:center;justify-content:flex-end;gap:8px;padding-right:14px}
.share{display:flex;align-items:center;gap:4px}
.share-btn{height:20px;padding:0 7px;border:1px solid #c8c8c8;border-radius:3px;background:linear-gradient(#fff,#e9e9e9);font-size:11px;color:#333;display:flex;align-items:center;gap:4px}
.share-btn i{width:10px;height:10px;background:#8a9bbf;display:inline-block}
.share-count{height:20px;padding:0 6px;border:1px solid #ccc;background:#fff;font-size:10px;color:#444;display:flex;align-items:center}
.share-count.wide{width:50px;justify-content:center}
.pager{position:absolute;left:352px;top:2114px;display:flex;gap:9px}
.pager span{height:22px;min-width:24px;padding:0 6px;border:1px solid #d2d2d2;background:#f8f8f8;font-size:10px;color:#666;display:flex;align-items:center;justify-content:center}

/* testimonials */
.testimonial{position:absolute;left:22px;width:330px;height:80px}
.avatar{position:absolute;left:0;top:0;width:79px;height:59px;background:linear-gradient(135deg,#6f6a66,#c9ad97 55%,#3e3a38)}
.quote{position:absolute;left:93px;top:0;width:210px;font-size:12px;line-height:17px;color:#777;font-weight:300}
.stamp{position:absolute;left:93px;top:54px;font-size:13px;color:#333}
.stamp b{font-weight:400;margin-left:22px}

/* comments plugin */
.plugin-head{position:absolute;left:0;top:0;width:100%;height:53px;background:var(--social);color:#fff;font-size:24px;font-weight:300;padding:12px 28px}
.plugin-circle{position:absolute;right:20px;top:8px;width:46px;height:46px;border-radius:50%;background:#7d93bf;border:3px solid #c4cfe6}
.login-btn{position:absolute;left:22px;top:76px;width:73px;height:36px;background:var(--social-deep);border:1px solid #3f5a8c;color:#fff;font-size:18px;font-weight:500;display:flex;align-items:center;justify-content:center}
.login-note{position:absolute;left:113px;top:80px;width:190px;font-size:13px;line-height:17px;color:#777}
.comment{position:absolute;left:22px;width:320px;height:60px}
.comment .avatar{width:59px}
.comment-text{position:absolute;left:80px;top:2px;width:218px;font-size:12px;line-height:18px;color:var(--link)}
.comment-meta{font-size:10.5px;color:#888;line-height:16px}
.plugin-foot{position:absolute;left:22px;top:500px;width:308px;display:flex;align-items:center;font-size:13px;color:#222}
.plugin-foot .sq{width:20px;height:20px;background:var(--social-deep);margin-right:16px}

/* footer */
.site-footer{position:absolute;left:0;top:2224px;width:1200px;height:93px;background:var(--charcoal)}
.footer-nav{position:absolute;right:96px;top:24px;display:flex;gap:24px;font-size:13px;color:#e6e6e6}
.copyright{position:absolute;right:96px;top:49px;font-size:12px;color:#9a9a9a}
.social{position:absolute;left:100px;top:35px;display:flex;gap:8px}
.social span{width:32px;height:32px;border-radius:50%;background:#f2f2f2}
</style>
</head>
<body>

<header class="site-header">
  <div class="utility-links">Login | Help | Support</div>
  <div class="brand"><span class="brand-dot"></span><span class="brand-name">LeadershipGuideNest.example</span></div>
  <div class="search">
    <svg width="13" height="13" viewBox="0 0 13 13"><circle cx="5.5" cy="5.5" r="4" fill="none" stroke="#777" stroke-width="1.6"/><line x1="8.5" y1="8.5" x2="12" y2="12" stroke="#777" stroke-width="1.8"/></svg>
    Search
  </div>
  <nav class="main-nav">
    <div class="nav-home">
      <svg width="24" height="22" viewBox="0 0 24 22"><path d="M12 2 L2 11 H5 V20 H10 V14 H14 V20 H19 V11 H22 Z" fill="#fff"/></svg>
    </div>
    <span class="nav-item" style="left:149px">About</span>
    <span class="nav-item" style="left:230px">Work With Us</span>
    <span class="nav-item" style="left:367px">Testimonials</span>
    <span class="nav-item" style="left:492px">Giving Back</span>
    <span class="nav-item" style="left:608px">Contact Us</span>
  </nav>
</header>

<div class="hero-band"></div>
<div class="hero-strip"></div>
<div class="hero-shadow"></div>
<section class="hero" role="img" aria-label="Photo of four smiling business professionals">
  <div class="slider-dots"><span></span><span></span><span class="active"></span><span></span><span></span></div>
  <div class="hero-caption">
    <div class="hero-title">Leadership Guide Nest</div>
    <p class="hero-text">Lorem Ipsum is simply dummy text of the printing and type-setting industry. Lorem Ipsum has been the industry's standard dummy text ever since the 1500s</p>
    <div class="resource-btn">RESOURCE DOWNLOAD
      <span class="plus"><svg width="12" height="12" viewBox="0 0 12 12"><path d="M6 1V11M1 6H11" stroke="#d99a3a" stroke-width="2.4"/></svg></span>
    </div>
  </div>
</section>

<h2 class="section-title" style="left:99px;top:798px">VIDEOS</h2>
<section class="panel" style="left:97px;top:831px;width:630px;height:284px">
  <div class="video-main">
    <div class="video-picture" role="img" aria-label="Video still of young people looking at a phone"></div>
    <svg class="play-overlay" width="56" height="56" viewBox="0 0 56 56"><circle cx="28" cy="28" r="26" fill="#222" stroke="#fff" stroke-width="3"/><path d="M22 16 L40 28 L22 40 Z" fill="#fff"/></svg>
    <div class="video-controls">
      <svg width="10" height="10" viewBox="0 0 10 10"><path d="M1 0 L9 5 L1 10 Z" fill="#fff"/></svg>
      <span>00:26</span>
      <div class="progress"><i></i><b></b></div>
      <span>00:33</span>
      <svg width="28" height="10" viewBox="0 0 28 10"><path d="M0 3H3L6 0V10L3 7H0Z" fill="#fff"/><rect x="10" y="4" width="16" height="2" fill="#e7b04f"/></svg>
      <svg width="12" height="12" viewBox="0 0 12 12"><path d="M0 0H4M0 0V4M12 0H8M12 0V4M0 12H4M0 12V8M12 12H8M12 12V8" stroke="#fff" stroke-width="2"/></svg>
    </div>
  </div>
  <div class="thumb" style="top:20px" role="img" aria-label="Video thumbnail of a team meeting"></div>
  <div class="thumb" style="top:113px" role="img" aria-label="Video thumbnail of colleagues talking"></div>
  <div class="thumb" style="top:205px" role="img" aria-label="Video thumbnail of an office group"></div>
</section>

<h2 class="section-title" style="left:758px;top:798px">OPTION FORM</h2>
<section class="panel" style="left:752px;top:831px;width:351px;height:284px">
  <div class="field" style="top:9px;height:34px">Name</div>
  <div class="field" style="top:54px;height:33px">E-mail Address</div>
  <div class="field" style="top:97px;height:33px">Mobile Number</div>
  <div class="field" style="top:142px;height:86px">Message</div>
  <div class="submit-btn">SUBMIT</div>
</section>

<h2 class="section-title" style="left:97px;top:1150px">BLOG</h2>

<article class="post" style="top:1190px">
  <div class="post-head">The standard Lorem Ipsum passage, used since the 1500s</div>
  <div class="post-image" style="background:linear-gradient(120deg,#5c6a78,#c8d2dc 50%,#3d4650)" role="img" aria-label="Photo of a boardroom presentation"></div>
  <p class="post-text">Lorem ipsum dolor sit amet, consectetur adipisicing elit, sed do eiusmod tempor incididunt ut labore et dolore magna aliqua. Ut enim ad minim veniam, quis nostrud exercitation ullamco laboris nisi ut aliquip ex ea commodo consequat. Duis aute irure dolor in reprehenderit in voluptate velit esse cillum dolore eu fugiat nulla pariatur. Excepteur sint occaecat cupidatat non proident, sunt in culpa qui officia deserunt mollit anim id est laborum.</p>
  <div class="read-more">READ MORE</div>
  <div class="share-row">
    <div class="share"><span class="share-btn"><i></i>Like</span><span class="share-count">164</span></div>
    <div class="share"><span class="share-btn"><i></i>Post</span><span class="share-count">200</span></div>
    <div class="share"><span class="share-btn">Plus</span><span class="share-count">4</span></div>
    <div class="share"><span class="share-btn">Save</span><span class="share-count wide">11</span></div>
  </div>
</article>

<article class="post" style="top:1503px">
  <div class="post-head">1914 translation by J. Whitcombe</div>
  <div class="post-image" style="background:linear-gradient(120deg,#3e3e44,#d7d1c8 50%,#6b625a)" role="img" aria-label="Photo of colleagues reviewing plans at a desk"></div>
  <p class="post-text">Lorem ipsum dolor sit amet, consectetur adipisicing elit, sed do eiusmod tempor incididunt ut labore et dolore magna aliqua. Ut enim ad minim veniam, quis nostrud exercitation ullamco laboris nisi ut aliquip ex ea commodo consequat. Duis aute irure dolor in reprehenderit in voluptate velit esse cillum dolore eu fugiat nulla pariatur. Excepteur sint occaecat cupidatat non proident, sunt in culpa qui officia deserunt mollit anim id est laborum.</p>
  <div class="read-more">READ MORE</div>
  <div class="share-row">
    <div class="share"><span class="share-btn"><i></i>Like</span><span class="share-count">164</span></div>
    <div class="share"><span class="share-btn"><i></i>Post</span><span class="share-count">200</span></div>
    <div class="share"><span class="share-btn">Plus</span><span class="share-count">4</span></div>
    <div class="share"><span class="share-btn">Save</span><span class="share-count wide">11</span></div>
  </div>
</article>

<article class="post" style="top:1816px">
  <div class="post-head">1914 translation by J. Whitcombe</div>
  <div class="post-image" style="background:linear-gradient(110deg,#9a6e52,#e0c6b0 45%,#b88a6c 75%,#d9c0a8)" role="img" aria-label="Photo of three smiling professionals"></div>
  <p class="post-text">Lorem ipsum dolor sit amet, consectetur adipisicing elit, sed do eiusmod tempor incididunt ut labore et dolore magna aliqua. Ut enim ad minim veniam, quis nostrud exercitation ullamco laboris nisi ut aliquip ex ea commodo consequat. Duis aute irure dolor in reprehenderit in voluptate velit esse cillum dolore eu fugiat nulla pariatur. Excepteur sint occaecat cupidatat non proident, sunt in culpa qui officia deserunt mollit anim id est laborum.</p>
  <div class="read-more">READ MORE</div>
  <div class="share-row">
    <div class="share"><span class="share-btn"><i></i>Like</span><span class="share-count">164</span></div>
    <div class="share"><span class="share-btn"><i></i>Post</span><span class="share-count">200</span></div>
    <div class="share"><span class="share-btn">Plus</span><span class="share-count">4</span></div>
    <div class="share"><span class="share-btn">Save</span><span class="share-count wide">11</span></div>
  </div>
</article>

<nav class="pager">
  <span>PREV</span><span>1</span><span>2</span><span>3</span><span>4</span><span>5</span><span>6</span><span>...</span><span>22</span><span>NEXT</span>
</nav>

<h2 class="section-title" style="left:766px;top:1150px">TESTIMONIALS</h2>
<section class="panel" style="left:752px;top:1188px;width:351px;height:444px">
  <div class="testimonial" style="top:20px">
    <div class="avatar" role="img" aria-label="Portrait of a client"></div>
    <p class="quote">" Lorem Ipsum is simply dummy text of the printing and typesetting industry. "</p>
    <div class="stamp">Nov 18,2012 <b>2.30 PM</b></div>
  </div>
  <div class="testimonial" style="top:117px">
    <div class="avatar" role="img" aria-label="Portrait of a client"></div>
    <p class="quote">" Lorem Ipsum is simply dummy text of the printing and typesetting industry. "</p>
    <div class="stamp">Nov 18,2012 <b>2.30 PM</b></div>
  </div>
  <div class="testimonial" style="top:216px">
    <div class="avatar" role="img" aria-label="Portrait of a client"></div>
    <p class="quote">" Lorem Ipsum is simply dummy text of the printing and typesetting industry. "</p>
    <div class="stamp">Nov 18,2012 <b>2.30 PM</b></div>
  </div>
  <div class="testimonial" style="top:313px">
    <div class="avatar" role="img" aria-label="Portrait of a client"></div>
    <p class="quote">" Lorem Ipsum is simply dummy text of the printing and typesetting industry. "</p>
    <div class="stamp">Nov 18,2012 <b>2.30 PM</b></div>
  </div>
  <div class="read-more" style="left:202px;top:410px;width:124px">READ MORE</div>
</section>

<section class="panel" style="left:752px;top:1649px;width:351px;height:529px;background:var(--white);box-shadow:0 14px 16px -10px rgba(0,0,0,.35)">
  <div class="plugin-head">Circlebook Comments<span class="plugin-circle"></span></div>
  <div class="login-btn">Login</div>
  <p class="login-note">You need to be logged into to see comments</p>
  <div class="abs" style="left:22px;top:135px;width:308px;height:1px;background:var(--line)"></div>
  <div class="comment" style="top:150px"><div class="avatar" role="img" aria-label="Commenter portrait"></div><p class="comment-text">Lorem Ipsum is simply dummy text of the printing and typesetting industry.<br><span class="comment-meta">6 People Viewed your Comments</span></p></div>
  <div class="comment" style="top:234px"><div class="avatar" role="img" aria-label="Commenter portrait"></div><p class="comment-text">Lorem Ipsum is simply dummy text of the printing and typesetting industry.<br><span class="comment-meta">6 People Viewed your Comments</span></p></div>
  <div class="comment" style="top:320px"><div class="avatar" role="img" aria-label="Commenter portrait"></div><p class="comment-text">Lorem Ipsum is simply dummy text of the printing and typesetting industry.<br><span class="comment-meta">6 People Viewed your Comments</span></p></div>
  <div class="comment" style="top:405px"><div class="avatar" role="img" aria-label="Commenter portrait"></div><p class="comment-text">Lorem Ipsum is simply dummy text of the printing and typesetting industry.<br><span class="comment-meta">6 People Viewed your Comments</span></p></div>
  <div class="abs" style="left:22px;top:482px;width:308px;height:1px;background:var(--line)"></div>
  <div class="plugin-foot"><span class="sq"></span>Circlebook Plugin<span style="margin-left:auto" class="share"><span class="share-btn"><i></i>Like</span><span class="share-count">203K</span></span></div>
</section>

<footer class="site-footer">
  <div class="social"><span></span><span></span><span></span></div>
  <nav class="footer-nav"><span>Home</span><span>About</span><span>Work With Us</span><span>Testimonials</span><span>Giving Back</span><span>Contact Us</span></nav>
  <div class="copyright">Copyright ©2012 leadership guide nest &nbsp;- All rights reserved</div>
</footer>

</body>
</html>
```